Steadfast Greenwell HEMP Cannabis CBD tinctures

We need packaging for our line of CBD product label design based in Oakland Ca Brand is called 'Steadfast Greenwell'. Our initial product is tincture to help people with pain with out the High effect of THC. I will be attaching og other company sample. The design should communicate slick look and relay health. Use the logo as way to color

Target Market(s)

CBD

Font styles to use
Serif
Decorative

Requirements
Must have
• Design that will make it stand out from the rest of the product on the shelve and be bright.
Nice to have
• The package must be able to stand out and not be dominated by Black color the green color must be the main color.
Should not have
• Be all black and get lost on the shelves

```html
<!DOCTYPE html>
<html lang="en">
<head>
<meta charset="utf-8">
<title>Steadfast Greenwell CBD Tincture Label</title>
<link href="https://fonts.googleapis.com/css2?family=Montserrat:wght@300;600;700&family=Oswald:wght@500;600&display=swap" rel="stylesheet">
<style>
  :root {
    --bg: #eef8e6;
    --label-white: #ffffff;
    --green: #3dbb4f;
    --green-bright: #4cc85c;
    --green-deep: #2a9a3b;
    --grey-line: #a9aaa9;
    --grey-text: #8a8a8a;
  }
  * { box-sizing: border-box; margin: 0; padding: 0; }
  html, body { width: 1200px; height: 1200px; overflow: hidden; }
  body {
    background: radial-gradient(circle at 50% 45%, #f7fcf2 0%, var(--bg) 75%);
    display: flex; align-items: center; justify-content: center;
  }
  .label {
    position: relative;
    width: 760px; height: 960px;
    background: var(--label-white);
    overflow: hidden;
    box-shadow: 0 10px 40px rgba(40, 90, 40, 0.12);
  }
  .label-pattern {
    position: absolute; inset: 0;
    background: linear-gradient(160deg, #f6fbf5 0%, #ffffff 45%, #f2faf2 100%);
  }
  .top-band {
    position: absolute; top: 0; left: 0; right: 0; height: 18px;
    background: var(--green-bright);
    border-bottom: 6px solid #d6d8d6;
  }
  .product-tab {
    position: absolute; top: 18px; left: 50%; transform: translateX(-50%);
    width: 226px; height: 50px;
    background: var(--green-bright);
    border-radius: 0 0 10px 10px;
    color: #fff;
    font: 300 33px/50px "Montserrat", sans-serif;
    text-align: center; letter-spacing: 0.5px;
  }
  .brand {
    position: absolute; top: 150px; left: 0; right: 0;
    display: flex; flex-direction: column; align-items: center; gap: 44px;
  }
  .brand-square {
    width: 150px; height: 150px;
    border: 18px solid var(--green);
    border-radius: 22px;
  }
  .brand-name {
    font: 600 52px/1 "Montserrat", sans-serif;
    color: var(--green);
    letter-spacing: -0.5px;
  }
  .strength-column {
    position: absolute; left: 50%; transform: translateX(-50%);
    top: 800px; bottom: 0; width: 288px;
    background: var(--green-deep);
  }
  .cbd-badge {
    position: absolute; left: 50%; transform: translateX(-50%);
    top: 470px; width: 276px; height: 150px;
  }
  .cbd-badge svg { position: absolute; inset: 0; }
  .cbd-word {
    position: absolute; left: 0; right: 0; top: 28px;
    font: 600 96px/1 "Oswald", sans-serif;
    color: #fff; text-align: center;
    transform: scaleX(0.82);
  }
  .extract-row {
    position: absolute; left: 50%; transform: translateX(-50%);
    top: 638px; width: 330px; height: 52px;
    border-top: 4px solid var(--grey-line);
    border-bottom: 4px solid var(--grey-line);
    background: #fff;
    font: 700 31px/44px "Montserrat", sans-serif;
    color: var(--green); text-align: center; letter-spacing: 1px;
  }
  .strength {
    position: absolute; left: 0; right: 0; top: 700px;
    font: 600 104px/1 "Oswald", sans-serif;
    color: var(--green-deep); text-align: center;
    transform: scaleX(0.82);
  }
  .bottom-band {
    position: absolute; left: 0; right: 0; bottom: 0; height: 136px;
    background: var(--green-bright);
    border-top: 6px solid var(--green);
  }
  .volume {
    position: absolute; left: 50%; transform: translateX(-50%);
    bottom: 0; width: 288px; height: 136px;
    background: var(--green-deep);
    color: #fff;
    font: 300 34px/1 "Montserrat", sans-serif;
    display: flex; align-items: center; justify-content: center;
    padding-top: 30px;
  }
</style>
</head>
<body>
  <main class="label">
    <div class="label-pattern" role="img" aria-label="Faint green outlined cube pattern across the white label"></div>
    <div class="top-band"></div>
    <div class="product-tab">TINCTURE</div>

    <div class="brand">
      <div class="brand-square"></div>
      <div class="brand-name">Steadfast Greenwell</div>
    </div>

    <div class="cbd-badge">
      <svg viewBox="0 0 276 150" width="276" height="150" aria-hidden="true">
        <polygon points="0,30 138,0 276,30 276,150 0,150" fill="#2a9a3b"/>
        <polygon points="10,36 138,10 266,36 266,150 10,150" fill="#3dbb4f"/>
      </svg>
      <div class="cbd-word">CBD</div>
    </div>

    <div class="extract-row">HEMP EXTRACT</div>
    <div class="strength">1500MG</div>

    <div class="bottom-band"></div>
    <div class="volume">15ml</div>
  </main>
</body>
</html>
```